Sell the dream! Property investment proposal document

We are looking for a proposal document which outlines our vision for property development. The purpose of the document is to raise investment from investors - sell the dream!
Brief summary:
Kestrel Dwellings Developments, is an emerging New Zealand property investment company with a focus on providing unique property investment opportunities.
Our expertise and capabilities in architectural modular homes provide us with a remarkable advantage in tackling the development of properties that are typically considered challenging, remote, or uniquely positioned.
Our specialization in this niche sector of property development not only sets us apart from competitors, but also paves the way for lucrative investment opportunities in the New Zealand property market.
Feel free to use any images from www.kestreldwellings.co.nz
Target Market(s)
investors for a unique property development opportunity
Industry/Entity Type
luxury property development in unique locations throughout New Zealand
Colors
Designer to choose only greyscale colors for use in the design.
Look and feel

```html
<!DOCTYPE html>
<html lang="en">
<head>
<meta charset="utf-8">
<title>Kestrel Dwellings Developments – Investment Proposal</title>
<link rel="stylesheet" href="https://fonts.googleapis.com/css2?family=Inter:wght@400;600&family=Montserrat:wght@300;400;600;700&display=swap">
<style>
:root{
  --bg:#e9e9e9;
  --ink-dark:#2b2929;
  --paper:#f6f6f6;
  --text-light:#e6e6e6;
  --text-dark:#2e2e2e;
  --dot-1:#d8d8d8;
  --dot-2:#a9a9a9;
  --dot-3:#7a7a7a;
  --dot-4:#4e4e4e;
}
*{margin:0;padding:0;box-sizing:border-box}
html,body{width:1200px;height:2400px;overflow:hidden;background:var(--bg)}
body{position:relative;font-family:"Inter",Arial,sans-serif}
.spread{position:absolute;left:80px;width:1040px;height:412px;background:var(--paper);box-shadow:0 6px 18px rgba(0,0,0,.12);overflow:hidden}
.spread::after{content:"";position:absolute;left:510px;top:0;width:20px;height:100%;background:linear-gradient(90deg,rgba(0,0,0,0),rgba(0,0,0,.12) 50%,rgba(0,0,0,0));pointer-events:none}
.spread--overview{top:240px}
.spread--origins{top:1040px}
.spread--financial{top:1841px}
.photo{position:absolute}
.panel{position:absolute;background:var(--ink-dark);color:var(--text-light)}
.heading{font-family:"Montserrat",Arial,sans-serif;font-size:17px;letter-spacing:.16em;text-transform:uppercase;line-height:1.3;font-weight:300}
.heading strong{font-weight:700}
.heading--tight{letter-spacing:.02em}
.dots{display:flex;gap:7px;margin:18px 0 42px}
.dots span{width:5px;height:5px;border-radius:50%}
.dots span:nth-child(1){background:var(--dot-1)}
.dots span:nth-child(2){background:var(--dot-2)}
.dots span:nth-child(3){background:var(--dot-3)}
.dots span:nth-child(4){background:var(--dot-4)}
.dots--on-light span:nth-child(1){background:#5a5a5a}
.dots--on-light span:nth-child(2){background:#8a8a8a}
.dots--on-light span:nth-child(3){background:#b2b2b2}
.dots--on-light span:nth-child(4){background:#d8d8d8}
.body-copy p{font-size:7.2px;line-height:1.55;margin-bottom:9px}
.body-copy b{font-weight:600}
.light{position:absolute;color:var(--text-dark)}
.columns{display:flex;gap:26px}
.columns .body-copy{flex:1}
</style>
</head>
<body>

<section class="spread spread--overview">
  <div class="photo" style="left:0;top:0;width:662px;height:412px;background:linear-gradient(180deg,#a9bccd 0%,#d9dde0 42%,#3a3836 55%,#5d5a50 78%,#4a4740 100%)" role="img" aria-label="Black timber modular cabin with lit interior and wooden deck on a coastal hillside at dusk"></div>
  <div class="panel" style="left:662px;top:0;width:378px;height:412px;padding:66px 32px 0 53px">
    <h2 class="heading">Business <strong>Overview</strong></h2>
    <div class="dots"><span></span><span></span><span></span><span></span></div>
    <div class="body-copy">
      <p><b>Kestrel Dwellings Developments,</b> is an emerging New Zealand property investment company with a focus on providing unique property investment opportunities.</p>
      <p>Our expertise and capabilities in architectural modular homes provide us with a remarkable advantage in tackling the development of properties that are typically considered challenging, remote, or uniquely positioned.</p>
      <p>As a company, with 48 employees boasting a wealth of experience in handling complex architectural projects, making us well-equipped to navigate the intricacies and demands of such ventures.</p>
      <p>This advantage allows us to not only execute projects efficiently but also to deliver exceptional results within condensed time frames.</p>
      <p>By capitalizing on our ability to develop difficult, remote, or one-of-a-kind properties swiftly and effectively, Kestrel Dwellings Developments offers investors a rare chance to engage in projects that promise exceptional profitability in the New Zealand property market.</p>
      <p>Our specialization in this niche sector of property development not only sets us apart from competitors, but also paves the way for lucrative investment opportunities in the New Zealand property market.</p>
    </div>
  </div>
</section>

<section class="spread spread--origins">
  <div class="photo" style="left:0;top:0;width:188px;height:412px;background:linear-gradient(180deg,#a7b4c0 0%,#c9c6bd 45%,#d8b68c 58%,#4b4a48 72%,#6a6660 100%)" role="img" aria-label="Glass pavilion home on a gravel site overlooking the sea at sunset"></div>
  <div class="panel" style="left:188px;top:0;width:332px;height:412px;padding:70px 34px 0 40px">
    <h2 class="heading">Business<br><strong>Origins</strong></h2>
    <div class="dots"><span></span><span></span><span></span><span></span></div>
    <div class="body-copy">
      <p><b>Kestrel Dwellings Developments</b> was established with the goal of transforming the property investment market in New Zealand by introducing an innovative approach that centers on architectural modular designs and streamlined project timelines.</p>
      <p>Driven by our enthusiasm for architecture and real estate, we have expanded our successful business model to not only offer financial opportunities for investors but also to expand on our passion for high-end architectural design. With a wealth of experience accumulated over the past six years in the construction and the property market, we are pivoting to focus solely on our property development initiatives, presenting completed Kestrel projects to the market, in exclusive locations.</p>
      <p>These projects will boast high-quality standards, meticulous attention to detail and landscaping, and creative design elements.<br>By introducing completed Kestrel properties into the market, we aim to reach a wider audience, catering to individuals who prefer ready-to-occupy homes, over engaging in the design and construction process. This approach also simplifies the financing process for prospective buyers, as established properties are often preferred by financial lenders.</p>
    </div>
  </div>
  <div class="light" style="left:520px;top:0;width:254px;height:412px;padding:70px 24px 0 56px">
    <h2 class="heading heading--tight">Competitive<br><strong>Advantage</strong></h2>
    <div class="dots dots--on-light"><span></span><span></span><span></span><span></span></div>
    <div class="body-copy">
      <p>Our competitive advantage lies in the uniqueness of our property investment opportunities. Unlike traditional real estate companies, we focus on offering properties that are not only profitable but also aesthetically pleasing and unique.</p>
      <p>By catering to the tastes of architecture lovers, we set ourselves apart from the competition and attract a niche market of customers who appreciate the artistry and design of our projects.</p>
      <p>Additionally, the streamlined and condensed timelines facilitated by our modular approach provide quicker returns on investment.</p>
    </div>
  </div>
  <div class="photo" style="left:774px;top:0;width:266px;height:200px;background:linear-gradient(180deg,#9fb3c6 0%,#c7d0d6 25%,#5b6058 50%,#3f4438 100%)" role="img" aria-label="Dark timber cabin on a rugged clifftop above the ocean"></div>
  <div class="photo" style="left:774px;top:210px;width:266px;height:202px;background:linear-gradient(90deg,#cfcbc2 0%,#8e877c 40%,#4a4540 75%,#2e2b28 100%)" role="img" aria-label="Bedroom with floor-to-ceiling glazing, sheer curtains and a made bed"></div>
</section>

<section class="spread spread--financial">
  <div class="photo" style="left:0;top:0;width:520px;height:299px;background:linear-gradient(180deg,#b9c4cc 0%,#d6d8d6 28%,#3a3937 48%,#4a4945 72%,#6f7a58 90%,#5e6a4a 100%)" role="img" aria-label="Single-level black clad modern home with open glass doors, palms and landscaped lawn"></div>
  <div class="panel" style="left:0;top:299px;width:520px;height:113px"></div>
  <div class="photo" style="left:10px;top:307px;width:160px;height:98px;background:linear-gradient(180deg,#6e6862,#2e2b29)" role="img" aria-label="Dark modern kitchen interior"></div>
  <div class="photo" style="left:180px;top:307px;width:160px;height:98px;background:linear-gradient(90deg,#c9bfa8,#7a6e5e 55%,#3a3430)" role="img" aria-label="Warmly lit bedroom with large windows"></div>
  <div class="photo" style="left:350px;top:307px;width:160px;height:98px;background:linear-gradient(180deg,#d5d7d8,#6c6c6a 60%,#2e2d2c)" role="img" aria-label="Dining room with long table and glass walls"></div>
  <div class="panel" style="left:520px;top:0;width:520px;height:296px;padding:68px 28px 0 57px">
    <h2 class="heading heading--tight">Financial <strong>Summary</strong></h2>
    <div class="dots"><span></span><span></span><span></span><span></span></div>
    <div class="columns">
      <div class="body-copy">
        <p>In terms of financial projections, with each development, we anticipate a profit of 10%–20% which will be project dependent.</p>
        <p>This growth is fueled by the increasing demand for unique property investments in New Zealand and our ability to deliver high-quality services to the market in a condensed time frame, with heavily controlled costs.</p>
        <p>With a solid business model and a dedicated team, we are confident in our ability to achieve success and establish Kestrel Dwellings Investments as a trusted name in the industry.</p>
      </div>
      <div class="body-copy">
        <p>New Zealand's property market has been experiencing steady growth over the years, making it an attractive destination for property investors. With its beautiful landscapes and strong economy, New Zealand offers a diverse range of investment opportunities for both local and international investors. The demand for quality properties in prime locations continues to rise, creating a favorable environment for property investment companies like ours that can lean on our modular benefits of being able to reach unique and remote locations.</p>
      </div>
    </div>
  </div>
  <div class="photo" style="left:520px;top:296px;width:520px;height:116px;background:linear-gradient(180deg,#aab0b4 0%,#c6c8c6 35%,#2f2e2c 60%,#55594a 100%)" role="img" aria-label="Long low black home lit at dusk with trees behind"></div>
</section>

</body>
</html>
```